Indoor Air Restoration company needs graphic design for a 6x12 v nose trailer to wrap

We offer mold services, duct cleaning, water damage clean up and odor removal. "We find, fix and prevent mold, odor and allergen problems" is what we want to communicate on this trailer, which is a rolling billboard. We like the blue and orange color themes, as found in our logo. The company name is Brightwater Dwelling Services and the logo is attached below. We'd like to see our message clearly, company name and what we offer. We tend to lean towards white letters on a darker background (blue or orange) but are very open to outside ideas, as we are stuck! Our website is available for reference if that is helpful. www.brightwaterdwell.com The phone number to be printed on truck is 302-517-9046, Happy designing!!

Target Market(s)

Home owners

Industry/Entity Type

Indoor Air Quality, Mold Remediation

Font styles to use
Sans Serif

Colors
0054AA
0677BA
7BADD7
CADEEF
E8F1F8
F0912C
F2A743
F7CA91
FBE8D2
FDF5EE

Requirements
Must have
• our message, company name and phone
Nice to have
• services we offer (mold remediation, duct cleaning, water damage and odor removal
Should not have
• cartoon feel

```html
<!DOCTYPE html>
<html lang="en">
<head>
<meta charset="utf-8">
<title>Brightwater Dwelling Services – Trailer Wrap</title>
<link rel="stylesheet" href="https://fonts.googleapis.com/css2?family=Roboto+Condensed:wght@700;800&family=Fira+Sans+Condensed:wght@700&family=Gochi+Hand&family=Montserrat:wght@700&display=swap">
<style>
  :root {
    --page: #ffffff;
    --royal: #1b1bb0;
    --royal-deep: #12128f;
    --title-blue: #1a17a6;
    --sun: #f7ea1e;
    --amber: #fbb012;
    --amber-line: #f08a1a;
    --ink: #1d1d1d;
    --white: #ffffff;
    --photo-light: #dfe5ef;
    --highlight: #eef24a;
    --frame: #2a2a2a;
  }
  * { box-sizing: border-box; margin: 0; padding: 0; }
  html, body { width: 848px; height: 1200px; overflow: hidden; background: var(--page); }
  .canvas { position: relative; width: 848px; height: 1200px; }

  .wrap-panel {
    position: absolute;
    left: 74px; top: 429px;
    width: 685px; height: 342px;
    outline: 1px solid var(--frame);
    overflow: hidden;
  }
  .wrap-panel__art { position: absolute; inset: 0; width: 100%; height: 100%; display: block; }

  .brand-mark {
    position: absolute; left: 140px; top: 22px; width: 120px;
    display: flex; flex-direction: column; align-items: center; gap: 6px;
  }
  .brand-mark__square { width: 34px; height: 34px; background: var(--royal); }
  .brand-mark__name {
    font-family: "Roboto Condensed", sans-serif; font-weight: 700;
    font-size: 14px; line-height: 1.05; color: var(--royal);
    text-align: center; text-transform: uppercase;
  }

  .company-title {
    position: absolute; left: 268px; top: 30px; width: 340px;
    font-family: "Roboto Condensed", sans-serif; font-weight: 800;
    color: var(--title-blue); text-align: center; text-transform: uppercase;
    line-height: 1;
    white-space: nowrap;
  }
  .company-title__line1 { display: block; font-size: 31px; letter-spacing: -0.3px; }
  .company-title__line2 { display: block; font-size: 31px; margin-top: 2px; }

  .tagline {
    position: absolute; left: 420px; top: 130px; width: 248px;
    font-family: "Gochi Hand", sans-serif; font-size: 16px; line-height: 1.35;
    color: var(--ink); text-align: center;
  }
  .tagline span { background: var(--highlight); padding: 0 8px; }

  .services {
    position: absolute; left: 31px; top: 138px;
    font-family: "Fira Sans Condensed", sans-serif; font-weight: 700; color: var(--white);
  }
  .services__heading { font-size: 21px; text-decoration: underline; text-underline-offset: 3px; text-decoration-thickness: 2px; }
  .services__item { position: absolute; font-size: 22px; white-space: nowrap; }
  .services__item--mold  { left: 0;   top: 38px; }
  .services__item--water { left: 219px; top: 38px; }
  .services__item--duct  { left: 27px;  top: 80px; }
  .services__item--odor  { left: 200px; top: 80px; }

  .phone {
    position: absolute; left: 24px; top: 287px;
    display: flex; align-items: center; gap: 10px;
  }
  .phone__icon { width: 38px; height: 38px; display: block; }
  .phone__number {
    font-family: "Montserrat", sans-serif; font-weight: 700; font-size: 38px;
    color: var(--ink); letter-spacing: 1px; line-height: 1;
  }
</style>
</head>
<body>
<div class="canvas">
  <section class="wrap-panel">
    <svg class="wrap-panel__art" viewBox="0 0 685 342" preserveAspectRatio="none">
      <defs>
        <linearGradient id="sunGlow" x1="0" y1="0" x2="1" y2="0">
          <stop offset="0" stop-color="#fbb315"/>
          <stop offset="0.45" stop-color="#f7ea1e"/>
          <stop offset="1" stop-color="#fbb315"/>
        </linearGradient>
        <linearGradient id="royalBand" x1="0" y1="0" x2="0" y2="1">
          <stop offset="0" stop-color="#2222c4"/>
          <stop offset="1" stop-color="#12129a"/>
        </linearGradient>
        <linearGradient id="photoFade" x1="0" y1="0" x2="1" y2="0">
          <stop offset="0" stop-color="#b8c4e0" stop-opacity="0"/>
          <stop offset="0.3" stop-color="#c4cde3" stop-opacity="0.85"/>
          <stop offset="0.6" stop-color="#e6eaf2"/>
          <stop offset="1" stop-color="#f4f5f8"/>
        </linearGradient>
      </defs>
      <rect width="685" height="342" fill="var(--amber)"/>
      <path d="M0,0 H685 V130 C600,120 450,132 330,137 C200,140 100,112 0,55 Z" fill="url(#sunGlow)"/>
      <path d="M0,55 C100,112 200,140 330,137 C450,132 600,120 685,130 V314 C640,282 560,256 470,258 C350,262 250,286 160,279 C80,273 30,263 0,253 Z" fill="url(#royalBand)"/>
      <g role="img" aria-label="Photo of a smiling family with children relaxing at home">
        <path d="M340,134 C450,130 600,120 685,130 V314 C640,282 560,256 470,258 C420,260 380,266 340,271 Z" fill="url(#photoFade)"/>
      </g>
      <path d="M0,55 C100,112 200,140 330,137 C450,132 600,120 685,130" fill="none" stroke="var(--amber-line)" stroke-width="2"/>
      <path d="M0,253 C30,263 80,273 160,279 C250,286 350,262 470,258 C560,256 640,282 685,314" fill="none" stroke="var(--royal-deep)" stroke-width="2"/>
    </svg>

    <div class="brand-mark">
      <span class="brand-mark__square"></span>
      <span class="brand-mark__name">Brightwater<br>Dwelling Services</span>
    </div>

    <h1 class="company-title">
      <span class="company-title__line1">Brightwater Dwelling</span>
      <span class="company-title__line2">Services</span>
    </h1>

    <p class="tagline"><span>We find, fix and prevent mold,</span><br><span>odor and allergen problems</span></p>

    <div class="services">
      <h2 class="services__heading">Our services:</h2>
      <span class="services__item services__item--mold">• Mold Remediation</span>
      <span class="services__item services__item--water">• Water Damage</span>
      <span class="services__item services__item--duct">• Duct Cleaning</span>
      <span class="services__item services__item--odor">• Odor Removal</span>
    </div>

    <div class="phone">
      <svg class="phone__icon" viewBox="0 0 38 38" aria-hidden="true">
        <defs>
          <linearGradient id="keyMetal" x1="0" y1="0" x2="1" y2="1">
            <stop offset="0" stop-color="#f2f2f2"/>
            <stop offset="1" stop-color="#9a9a9a"/>
          </linearGradient>
        </defs>
        <rect x="1" y="1" width="36" height="36" rx="5" fill="url(#keyMetal)" stroke="#7a7a7a"/>
        <path d="M16,9 C13,10 12,13 12,19 C12,25 13,28 16,29 L18,28 L17,23 L15,23 C14.5,21 14.5,17 15,15 L17,15 L18,10 Z" fill="#2a2a2a"/>
      </svg>
      <span class="phone__number">302-517-9046</span>
    </div>
  </section>
</div>
</body>
</html>
```